brqnal new business card design project

we need a new business card design. you can view info about us @ brqnal-example.com. i have attached an example of our previous card with our previous name that we no longer use. We really liked the design, colors etc. look below to see more info about this project. it asks for a limited number of words. please see our website for more info about our compnay.

Target Market(s)

law enforcement

Contact Information for Business Card

i have uploaded an example of what we used before that we liked.

Font styles to use
Serif

```html
<!DOCTYPE html>
<html lang="en">
<head>
<meta charset="utf-8">
<title>brqnal business card</title>
<link href="https://fonts.googleapis.com/css2?family=Source+Serif+4:opsz,wght@8..60,300;8..60,400&display=swap" rel="stylesheet">
<style>
  :root {
    --backdrop: #c4c4c4;
    --card-dark: #04111c;
    --card-mid: #0a1d2e;
    --brand-blue: #1a86cc;
    --band-blue: #13669f;
    --band-light: #e4e6e8;
    --text-light: #e8edf2;
    --text-muted: #c3ccd4;
  }
  * { margin: 0; padding: 0; box-sizing: border-box; }
  html, body { width: 1200px; height: 576px; overflow: hidden; }
  body {
    position: relative;
    background: var(--backdrop);
    font-family: "Source Serif 4", Georgia, serif;
  }
  .card {
    position: absolute;
    top: 138px;
    width: 484px;
    height: 294px;
    border-radius: 14px;
    overflow: hidden;
    background: linear-gradient(160deg, var(--card-mid) 0%, var(--card-dark) 60%);
  }
  .card--front { left: 82px; }
  .card--back { left: 602px; }

  .map-area {
    position: absolute;
    left: 30px; top: 30px; width: 400px; height: 240px;
    background: radial-gradient(ellipse at 50% 55%, rgba(40,90,110,0.28) 0%, rgba(20,50,70,0.12) 50%, rgba(0,0,0,0) 75%);
  }
  .network-area {
    position: absolute;
    right: 0; top: 0; width: 240px; height: 294px;
    background: radial-gradient(ellipse at 70% 35%, rgba(50,90,140,0.35) 0%, rgba(20,45,80,0.18) 45%, rgba(0,0,0,0) 80%);
  }

  .wordmark {
    position: absolute;
    font-weight: 300;
    color: var(--text-light);
    letter-spacing: 0.05em;
    line-height: 1;
  }
  .card--front .wordmark { left: 0; right: 0; top: 112px; text-align: center; font-size: 56px; }
  .card--back .wordmark { left: 28px; top: 34px; font-size: 46px; }

  .contact-block { position: absolute; left: 26px; top: 112px; color: var(--text-muted); }
  .person-name { font-size: 19px; font-weight: 400; color: var(--brand-blue); line-height: 1.2; }
  .person-title { font-size: 12px; font-weight: 300; margin-top: 3px; color: var(--text-light); }
  .contact-list { list-style: none; margin-top: 16px; }
  .contact-list li {
    display: flex; align-items: center; gap: 10px;
    font-size: 12.5px; font-weight: 300; color: var(--text-light);
    height: 18px;
  }
  .contact-list svg { width: 11px; height: 11px; fill: var(--brand-blue); flex: none; }
  .address { font-size: 13px; font-weight: 300; color: var(--text-light); margin-top: 9px; }

  .bottom-bands { position: absolute; left: 0; bottom: 0; width: 484px; height: 24px; }
  .site-url {
    position: absolute; right: 22px; bottom: 7px;
    font-size: 10.5px; font-weight: 300; letter-spacing: 0.1em;
    color: var(--text-muted); line-height: 1;
  }
</style>
</head>
<body>

  <section class="card card--front">
    <div class="map-area" role="img" aria-label="Faint network-dot map of the country behind the name"></div>
    <div class="wordmark">BRQNAL</div>
    <svg class="bottom-bands" viewBox="0 0 484 24" aria-hidden="true">
      <polygon points="0,0 194,0 180,24 0,24" fill="var(--band-blue)"/>
      <polygon points="207,0 271,0 257,24 193,24" fill="var(--band-light)"/>
    </svg>
    <div class="site-url">www.brqnal-example.com</div>
  </section>

  <section class="card card--back">
    <div class="network-area" role="img" aria-label="Faint connected-node network pattern"></div>
    <div class="wordmark">BRQNAL</div>
    <div class="contact-block">
      <div class="person-name">Daniel Ashford</div>
      <div class="person-title">Founder/Chief Executive Officer</div>
      <ul class="contact-list">
        <li>
          <svg viewBox="0 0 12 12"><path d="M1 4 C1 2 3 1 6 1 S11 2 11 4 L9 5 L8 3.5 H4 L3 5 Z M3 6 H9 L10 11 H2 Z"/></svg>
          800.555.0142
        </li>
        <li>
          <svg viewBox="0 0 12 12"><path d="M0 2 H12 V10 H0 Z"/><path d="M0 2 L6 7 L12 2" fill="none" stroke="#04111c" stroke-width="1"/></svg>
          info@brqnal-example.com
        </li>
        <li>
          <svg viewBox="0 0 12 12"><circle cx="6" cy="6" r="5.5"/><path d="M0.5 6 H11.5 M6 0.5 V11.5 M6 0.5 C3 3 3 9 6 11.5 M6 0.5 C9 3 9 9 6 11.5" fill="none" stroke="#04111c" stroke-width="0.8"/></svg>
          www.brqnal-example.com
        </li>
      </ul>
      <div class="address">4120 Larkspur Avenue Dallas, TX 75204</div>
    </div>
    <svg class="bottom-bands" viewBox="0 0 484 24" aria-hidden="true">
      <polygon points="0,0 214,0 202,24 0,24" fill="var(--band-blue)"/>
      <polygon points="228,0 288,0 276,24 216,24" fill="var(--band-light)"/>
    </svg>
    <div class="site-url">www.brqnal-example.com</div>
  </section>

</body>
</html>
```